UK Online Auction Site needs a clever design

We need a contemporary landing page and registration page design for a UK auction website, that look equally at home on PC's and tablets . The design should be fresh, bright, clean, professional, robust, and familiar. We would like to see something clever but functional.

Online

```html
<!DOCTYPE html>
<html lang="en">
<head>
<meta charset="utf-8">
<title>Bidwell – UK Online Auctions</title>
<link href="https://fonts.googleapis.com/css2?family=Source+Sans+3:wght@400;600;700&family=Comfortaa:wght@300;400&family=Pacifico&display=swap" rel="stylesheet">
<style>
:root{
  --ink:#222;
  --text:#444;
  --muted:#777;
  --link:#1f5fbf;
  --blue:#1581d6;
  --blue-dark:#0a63b5;
  --black:#000;
  --header:#f3f3f3;
  --band:#e3e3e3;
  --line:#dcdcdc;
  --panel-border:#e4e4e4;
  --red:#e8321e;
  --orange:#f7911e;
  --white:#fff;
}
*{box-sizing:border-box;margin:0;padding:0}
html,body{width:1200px;height:998px;overflow:hidden;background:var(--white)}
body{position:relative;font-family:"Source Sans 3",Arial,sans-serif;color:var(--text)}
.abs{position:absolute}
a{color:var(--link);text-decoration:none}

.topbar{left:0;top:0;width:1200px;height:31px;background:var(--black);color:#999;font-size:13px}
.topbar p{position:absolute;right:126px;top:7px}
.topbar b{color:#eee;font-weight:400}

.header{left:0;top:31px;width:1200px;height:77px;background:linear-gradient(#fafafa,#eeeeee)}
.brand{left:116px;top:38px;width:180px;height:62px;display:flex;align-items:center;gap:8px}
.brand .mark{width:26px;height:26px;border-radius:50%;background:var(--blue)}
.brand span{font-size:34px;font-weight:700;color:var(--blue-dark)}
.nav{right:126px;top:64px;display:flex;gap:26px;font-size:13px;color:#555;font-family:Arial,sans-serif}
.nav li{list-style:none;display:flex;align-items:center;gap:7px}
.nav svg{display:block}

.band{left:0;top:108px;width:1200px;height:65px;background:var(--band)}
.cat-btn{left:110px;top:125px;width:182px;height:33px;background:#111;color:#fff;font-size:17px;padding:5px 0 0 17px}
.cat-btn svg{position:absolute;right:14px;top:13px}
.search-label{left:407px;top:131px;font-size:17px;color:#333}
.search-box{left:464px;top:128px;width:561px;height:30px;background:#fff;border:1px solid #e0e0e0}
.search-box .scope{position:absolute;left:0;top:0;height:28px;width:110px;border-right:1px solid #ddd;font-size:14px;color:#222;padding:5px 0 0 13px}
.search-box .gear{position:absolute;right:10px;top:7px}
.search-btn{left:1031px;top:128px;width:45px;height:30px;background:var(--blue);border-radius:3px}
.search-btn svg{position:absolute;left:12px;top:5px}
.more{left:1034px;top:172px;width:30px;height:13px;background:#e6e6e6;border-radius:0 0 3px 3px;display:flex;justify-content:center;gap:3px;padding-top:4px}
.more i{width:5px;height:5px;border-radius:50%;background:#555}

.cat-list{left:110px;top:158px;width:210px;height:303px;background:#fff;border:1px solid #ccc;border-top:3px solid #111;list-style:none;padding-top:7px}
.cat-list li{height:29px;margin:0 2px;border-bottom:1px solid #e2e2e2;font-size:14px;color:#444;padding:7px 0 0 15px;position:relative;letter-spacing:.2px}
.cat-list li:last-child{border-bottom:none}
.cat-list li.all{font-weight:700;color:#333}
.cat-list li::after{content:"›";position:absolute;right:12px;top:4px;font-size:15px;color:#333}

.promo{font-family:"Comfortaa",sans-serif}
.promo .pct{left:360px;top:198px;font-size:56px;font-weight:300;color:var(--red)}
.promo .pct small{font-size:30px;color:#333}
.promo .line1{left:356px;top:270px;font-size:28px;color:#333;letter-spacing:1px}
.promo .line2{left:353px;top:300px;font-size:48px;color:var(--orange);font-weight:300}
.promo .line3{left:361px;top:362px;font-size:16px;color:#1a4d6e;letter-spacing:1px}
.view-all{left:358px;top:408px;width:88px;height:24px;border-radius:12px;background:#333;color:#fff;font-size:12px;padding:4px 0 0 10px;font-family:"Comfortaa",sans-serif}
.hero-photo{left:662px;top:282px;width:358px;height:172px;background:radial-gradient(ellipse at 45% 50%,#5a5a5a 0%,#2a2a2a 45%,#eaeaea 75%,#fff 100%)}
.sticker{left:876px;top:190px;width:156px;height:90px;overflow:hidden}
.sticker div{position:absolute;left:0;top:-66px;width:156px;height:156px;border-radius:50%;background:radial-gradient(circle at 50% 35%,#ff5a3a,var(--red) 70%)}
.sticker p{position:absolute;left:0;width:156px;text-align:center;color:#fff;font-size:20px;line-height:27px;top:6px;font-family:"Comfortaa",sans-serif}
.pager{left:978px;top:451px;display:flex;gap:8px}
.pager span{width:20px;height:21px;border:1px solid #ddd;font-size:11px;color:#888;text-align:center;padding-top:3px;font-family:Arial,sans-serif}

.panels{left:108px;top:499px;width:672px;height:255px;border:4px solid var(--panel-border);display:flex}
.panel{height:100%;border-right:4px solid var(--panel-border);padding:10px 12px}
.panel:last-child{border-right:none}
.panel h2{font-size:19px;font-weight:600;color:var(--ink);margin-bottom:8px}
.panel p{font-size:13px;line-height:16px;color:#555}
.welcome{width:208px}
.welcome ul{list-style:none;margin-top:16px}
.welcome li{font-size:13px;line-height:18px;padding-left:13px;position:relative}
.welcome li::before{content:"";position:absolute;left:2px;top:5px;border-left:6px solid #666;border-top:4px solid transparent;border-bottom:4px solid transparent}
.signin{width:222px;padding-left:16px}
.signin .btn{display:block;margin:30px 0 0 9px;width:165px;height:30px;border-radius:3px;background:linear-gradient(#1e90e0,var(--blue-dark));color:#fff;font-size:16px;text-align:center;padding-top:4px}
.signin .reg{margin-top:38px}
.confidence{flex:1;padding-left:8px}
.feature{display:flex;gap:12px;margin-bottom:10px}
.feature svg{flex:none;margin-top:2px}
.feature h3{font-size:14px;font-weight:600;color:#333}
.feature h3 span{font-weight:400;color:#555}
.ad{left:790px;top:499px;width:300px;height:256px;background:linear-gradient(#f2f2f2,#fafafa 60%,#f3f3f3);display:flex;align-items:center;justify-content:center;font-size:27px;color:#666;letter-spacing:-1px}

.footer-col{top:772px;font-size:14px}
.footer-col h4{font-size:14px;font-weight:600;color:#555;margin-bottom:5px}
.footer-col a{display:block;line-height:24px;padding-left:2px}
.footer-col .social{display:flex;align-items:center;gap:6px}
.footer-col .social i{width:18px;height:18px;border-radius:50%;display:inline-block}
.lang{left:893px;top:922px;width:158px;height:29px;border:1px solid #ddd;border-radius:2px;font-size:13px;color:#888;padding:6px 0 0 12px}
.lang svg{position:absolute;right:10px;top:11px}
.code{left:1076px;top:928px;font-size:12px;color:#999}
.legal{left:116px;top:950px;font-size:12px;line-height:24px;color:#555}
</style>
</head>
<body>

<div class="abs topbar"><p>Welcome! <b>Register</b> or <b>Sign In</b></p></div>

<header class="abs header"></header>
<div class="abs brand"><span class="mark"></span><span>Bidwell</span></div>
<ul class="abs nav">
  <li><svg width="16" height="14" viewBox="0 0 16 14"><circle cx="7" cy="8" r="5" fill="none" stroke="#333" stroke-width="2"/><rect x="9" y="1" width="6" height="4" fill="#333"/></svg>Sell ⌄</li>
  <li><svg width="20" height="14" viewBox="0 0 20 14"><circle cx="7" cy="4" r="3" fill="#333"/><path d="M1 14c0-5 12-5 12 0z" fill="#333"/><circle cx="14" cy="4" r="3" fill="#333"/><path d="M11 14c0-4 9-5 9 0z" fill="#333"/></svg>Sign In ⌄</li>
  <li><svg width="18" height="15" viewBox="0 0 18 15"><path d="M1 1h3l2 9h9l2-6H5" fill="none" stroke="#333" stroke-width="1.6"/><circle cx="7" cy="13" r="1.5" fill="#333"/><circle cx="14" cy="13" r="1.5" fill="#333"/></svg>Cart ⌄</li>
  <li><svg width="16" height="14" viewBox="0 0 16 14"><path d="M8 14L1 7a4 4 0 016-5l1 1 1-1a4 4 0 016 5z" fill="#333"/></svg>Favourite ⌄</li>
  <li><svg width="14" height="15" viewBox="0 0 14 15"><path d="M7 0l7 3v4c0 4-3 7-7 8-4-1-7-4-7-8V3z" fill="#333"/><path d="M4 7l2 2 4-4" stroke="#fff" stroke-width="1.6" fill="none"/></svg>Help ⌄</li>
</ul>

<div class="abs band"></div>
<div class="abs cat-btn">Short by Category<svg width="14" height="8" viewBox="0 0 14 8"><path d="M0 0h14L7 8z" fill="#fff"/></svg></div>
<div class="abs search-label">Search</div>
<div class="abs search-box">
  <div class="scope">All Categories ⌵</div>
  <svg class="gear" width="26" height="16" viewBox="0 0 26 16"><circle cx="8" cy="8" r="5" fill="none" stroke="#222" stroke-width="3" stroke-dasharray="2.5 1.4"/><circle cx="8" cy="8" r="2" fill="#222"/><path d="M19 6l3 3 3-3" fill="none" stroke="#222" stroke-width="1.5"/></svg>
</div>
<div class="abs search-btn"><svg width="22" height="22" viewBox="0 0 22 22"><circle cx="9" cy="9" r="6.5" fill="none" stroke="#fff" stroke-width="3"/><path d="M14 14l6 6" stroke="#fff" stroke-width="4" stroke-linecap="round"/></svg></div>
<div class="abs more"><i></i><i></i><i></i></div>

<ul class="abs cat-list">
  <li class="all">All categories</li>
  <li>Automotive</li>
  <li>Business &amp; Industrial</li>
  <li>Clothing and Accessories</li>
  <li>Digital Products</li>
  <li>Electronics</li>
  <li>For the Home</li>
  <li>Real Estate</li>
  <li>Watches</li>
  <li>The Great Outdoors</li>
</ul>

<section class="promo">
  <div class="abs pct">40%<small>OFF</small></div>
  <div class="abs line1">The Smartest</div>
  <div class="abs line2">Cameras</div>
  <div class="abs line3">Hurry! while supplies last</div>
  <div class="abs view-all">&gt; view all</div>
</section>
<div class="abs hero-photo" role="img" aria-label="Product photo of a compact digital camera with its flip-out screen"></div>
<div class="abs sticker"><div></div><p>Shop<br>Cameras</p></div>
<div class="abs pager"><span>1</span><span>2</span><span>3</span><span>4</span></div>

<section class="abs panels">
  <div class="panel welcome">
    <h2>Welcome</h2>
    <p>Even if you're new or already experienced, we have everything you need to enjoy shopping on Bidwell.</p>
    <ul>
      <li><a href="#">How do I pay for items?</a></li>
      <li><a href="#">How do I leave feedback?</a></li>
      <li><a href="#">How do I open a new store?</a></li>
      <li><a href="#">How do I place bids?</a></li>
      <li><a href="#">How do I ship my items?</a></li>
    </ul>
  </div>
  <div class="panel signin">
    <h2>Sign In</h2>
    <p>Sign-in to your account in order to buy, sell or manage your prefer-ences.</p>
    <a class="btn" href="#">Sign In</a>
    <p class="reg">Don't have an account? <a href="#">Register ›</a></p>
  </div>
  <div class="panel confidence">
    <h2>Shop with confidence</h2>
    <div class="feature">
      <svg width="36" height="40" viewBox="0 0 36 40"><path d="M18 1l16 6v10c0 11-7 18-16 22C9 35 2 28 2 17V7z" fill="#5a9a3a" stroke="#ccc" stroke-width="2"/><path d="M10 20l6 6 11-12" stroke="#fff" stroke-width="4" fill="none"/></svg>
      <div><h3>Completely safe</h3><p>Bid on or buy items you're watching or searching for</p></div>
    </div>
    <div class="feature">
      <svg width="36" height="44" viewBox="0 0 36 44"><path d="M8 2h20v10c0 8-4 13-10 13S8 20 8 12z" fill="#e8b422"/><path d="M8 6H2c0 8 4 11 8 11M28 6h6c0 8-4 11-8 11" fill="none" stroke="#e8b422" stroke-width="2"/><rect x="16" y="25" width="4" height="9" fill="#c99414"/><rect x="9" y="34" width="18" height="5" fill="#c99414"/></svg>
      <div><h3>Premium sellers</h3><p>Great service and the best delivery when you buy from premium sellers.</p></div>
    </div>
    <div class="feature">
      <svg width="36" height="34" viewBox="0 0 36 34"><rect x="1" y="4" width="34" height="12" rx="2" fill="#2f7fd8"/><path d="M6 10h3M12 10h3M18 10h3M24 10h3" stroke="#fff" stroke-width="2"/><path d="M24 14v12l3-3 3 6 2-1-3-6h4z" fill="#fff" stroke="#333" stroke-width="1.2"/></svg>
      <div><h3>Feedback <span>rating system</span></h3><p>View seller history and feedback of users before you bid or buy.</p></div>
    </div>
  </div>
</section>
<aside class="abs ad">Awesome Ad.</aside>

<nav class="abs footer-col" style="left:115px"><h4>bidwell.co.uk</h4><a href="#">Advertising</a><a href="#">Knowledge Base</a><a href="#">Forum</a><a href="#">Stores</a><a href="#">Want Ads</a></nav>
<nav class="abs footer-col" style="left:275px"><h4>Buy</h4><a href="#">Categories</a><a href="#">Search</a><a href="#">Currency Converter</a></nav>
<nav class="abs footer-col" style="left:427px"><h4>Sell</h4><a href="#">Sell New Item</a><a href="#">Sell Bulk Items</a></nav>
<nav class="abs footer-col" style="left:598px"><h4>Support</h4><a href="#">Contact</a><a href="#">Terms</a><a href="#">Privacy</a><a href="#">RSS</a></nav>
<nav class="abs footer-col" style="left:759px"><h4>Other</h4><a href="#">About</a><a href="#">News</a><a href="#">Feeds</a></nav>
<nav class="abs footer-col" style="left:933px"><h4>Stay connected</h4>
  <a class="social" href="#"><i style="background:#3b5998"></i>Friendbook</a>
  <a class="social" href="#"><i style="background:#2aa3ef"></i>Chirper</a>
  <a class="social" href="#"><i style="background:#dd4b39"></i>Circles</a>
</nav>

<div class="abs lang">English<svg width="10" height="6" viewBox="0 0 10 6"><path d="M0 0h10L5 6z" fill="#555"/></svg></div>
<div class="abs code">M1</div>
<div class="abs legal">© 2014.www.bidwell-example.com<br>All rights reserved</div>

</body>
</html>
```